Website Redesign for Non-Profit Ministry & Church

NOTE: Please do not contact me privately — all private inquiries will be ignored.

Individuals seeking spiritual healing, community connection, ministry support and journal-based encounters.

Description of What’s Needed

We need a clean, fresh, inviting website that encourages engagement and connection. The site should feel warm and accessible, draw people in, and clearly present who we are, what we offer, and how visitors can participate. The layout should be straightforward, with well-structured pages (no overlapping objects, minimal layering complexity) and easy to navigate. Use only Google Fonts. All stock photos must be sourced from royalty-free sites and include proper attribution. We will not include a search feature.

Pages to Create
1. Home Page – impactful hero area, clear call-to-action, visual story of ministry, giving/gathering invitation.
2. About Us – vision, mission, leadership, testimonies, history.
3. Meetings & Events – upcoming gatherings, schedule, how to attend, sign-up or interest form.
4. Encounter: “Lanterns by the River” (book) – dedicated page for the book, overview, purchase link or details, journal prompts, imagery.
5. Healing Rooms / Ministry – explain ministry offerings, invite participation, testimonials or case-studies.
6. Live Stream & Links Page – page listing links for YouTube live stream, other platforms, archive links; simple layout.

Colour & Branding

Use colours that blend with our existing logo (attached). The palette should feel contemporary, welcoming, and aligned with ministry themes of restoration, healing and love. Ensure text, button and link colours maintain good contrast for accessibility.

Existing Content & Reference

Please gather available content from our current website in the attachment here for text, images and structure for reuse.

Imagery Guidelines

– Use original photos from our Gatherly page or Google Location listing for building or people images when available.
– If generic images are used, ensure they depict appropriate ministry-related buildings or people (community, warm gathering) — avoid generic unrelated stock imagery.
– All photos must be royalty-free or have proper licensing and attribution.
– No overlapping objects or visual clutter; clean layouts with defined sections.

Additional Notes

– Integration: We currently utilise MailChimp for email communication; the design should include a connection/invite to subscribe (via MailChimp) but no blog page is required at this time.
– Payment/Giving: We accept PayPal and already have a giving portal; include clear donation/give buttons or calls-to-action linking to existing giving systems.
– No search function to be included.
– Layouts should avoid complex layering or overlapping elements—designers should work with distinct content blocks, clear visual hierarchy, and straightforward mobile-friendly structure.

Target Market(s)

Industry/Entity Type

Church/Religious institution

Number of Pages Required

5+ page

Requirements
Should not have
• search bar

```html
<!DOCTYPE html>
<html lang="en">
<head>
<meta charset="utf-8">
<title>Mended, Cherished, Whole — Home</title>
<link href="https://fonts.googleapis.com/css2?family=Plus+Jakarta+Sans:wght@400;500;600;700;800&display=swap" rel="stylesheet">
<style>
:root{
  --purple:#4a1470;
  --green-dark:#0a5e44;
  --green:#0f7a5a;
  --green-light:#1aa487;
  --ink:#222;
  --muted:#555;
  --night:#0d0d0d;
  --white:#fff;
}
*{box-sizing:border-box;margin:0;padding:0}
html,body{width:1200px;height:4428px;overflow:hidden}
body{position:relative;background:var(--white);font-family:"Plus Jakarta Sans",sans-serif;color:var(--ink)}
.abs{position:absolute}
.btn{position:absolute;display:flex;align-items:center;justify-content:center;border-radius:22px;color:var(--white);font-weight:600;font-size:14px;background:linear-gradient(90deg,var(--green-dark),var(--green-light));text-decoration:none;white-space:nowrap}
.brand{color:var(--white);font-weight:700;line-height:1;display:flex;align-items:center;gap:12px}
.brand-dot{border-radius:50%;border:3px solid var(--white);flex:none}

/* hero */
.hero{left:0;top:0;width:1200px;height:760px;overflow:hidden}
.hero-photo{position:absolute;inset:0;background:linear-gradient(160deg,#2d2a2e 0%,#4a3c38 35%,#2a2730 65%,#1a1820 100%)}
.hero-photo::after{content:"";position:absolute;inset:0;background:linear-gradient(90deg,rgba(0,0,0,.55),rgba(0,0,0,.15))}
.hero-wave{position:absolute;left:0;top:0}
.nav-links{position:absolute;left:395px;top:118px;display:flex;gap:52px;font-size:14px;color:var(--white);font-weight:500}
.hero h1{left:108px;top:243px;font-size:56px;font-weight:800;color:var(--white);line-height:1.17;letter-spacing:-.5px}
.hero p{left:111px;top:386px;width:420px;font-size:17px;line-height:32px;color:var(--white)}

/* mission */
.mission-art{left:110px;top:885px;width:500px;height:473px;border-radius:50%;background:radial-gradient(circle at 40% 35%,#f4d48a 0%,#c9872e 35%,#7a3e12 65%,rgba(255,255,255,0) 72%)}
.section-title{font-weight:800;color:var(--purple);font-size:44px;line-height:1.22;letter-spacing:-.5px}
.mission h2{left:667px;top:905px}
.mission p{left:667px;width:424px;font-size:16px;line-height:33px;color:var(--muted)}

/* why */
.why h2{left:0;top:1428px;width:1200px;text-align:center}
.why .lead{left:0;top:1485px;width:1200px;text-align:center;font-size:20px;line-height:34px;color:#333}
.feature{position:absolute;width:210px;text-align:center}
.feature .icon{width:112px;height:112px;margin:0 auto;border-radius:50%;border:3px solid var(--green);box-shadow:0 6px 14px rgba(0,0,0,.15);display:flex;align-items:center;justify-content:center;background:var(--white)}
.feature h3{margin-top:22px;font-size:17px;line-height:23px;font-weight:700;color:var(--green)}
.feature p{margin-top:12px;font-size:13px;line-height:23px;color:var(--muted)}

/* stories */
.stories-band{left:0;top:1960px}
.stories h2{left:0;top:2160px;width:1200px;text-align:center;font-size:48px;font-weight:800;color:var(--white);letter-spacing:-.5px}
.stories .lead{left:0;top:2230px;width:1200px;text-align:center;font-size:18px;line-height:34px;color:var(--white)}
.story-card{position:absolute;top:2331px;width:231px;height:329px;border-radius:22px;overflow:hidden;background:var(--green-dark)}
.story-card .photo{height:260px}
.story-card h3{padding-top:12px;text-align:center;font-size:16px;line-height:24px;font-weight:500;color:var(--white)}
.btn-light{background:var(--white);color:var(--green)}

/* social feed */
.feed h2{left:0;top:2975px;width:1200px;text-align:center}
.feed-photo{position:absolute;top:3062px;width:231px;height:329px;border-radius:22px;box-shadow:0 8px 18px rgba(0,0,0,.18)}

/* newsletter */
.news h2{left:0;top:3660px;width:1200px;text-align:center}
.news p{left:0;top:3720px;width:1200px;text-align:center;font-size:17px;line-height:31px;color:var(--muted)}
.email-field{left:270px;top:3795px;width:419px;height:52px;border:1px solid #ccc;border-radius:26px;padding-left:26px;display:flex;align-items:center;font-size:14px;color:#555}

/* footer */
.footer-wave{left:0;top:3860px}
.footer{left:0;top:4040px;width:1200px;height:388px;background:var(--night)}
.footer h4{position:absolute;font-size:20px;font-weight:600;color:var(--white)}
.footer ul{position:absolute;list-style:none;font-size:13px;color:var(--white)}
.footer li{display:flex;align-items:center;gap:12px;height:36px}
.footer .bullet{width:12px;height:12px;border-radius:50%;border:3px solid var(--white);flex:none}
.rule{left:110px;top:4366px;width:980px;border-top:1px dashed #555}
.copy{left:0;top:4392px;width:1200px;text-align:center;font-size:13px;color:var(--white)}
</style>
</head>
<body>

<!-- HERO -->
<section class="hero abs">
  <div class="hero-photo" role="img" aria-label="Photo of a speaker preaching to a seated congregation in a sanctuary"></div>
  <svg class="hero-wave" width="1200" height="760" viewBox="0 0 1200 760">
    <defs><linearGradient id="gw" x1="0" x2="1"><stop offset="0" stop-color="#0a5e44"/><stop offset="1" stop-color="#1aa487"/></linearGradient></defs>
    <path d="M0 570 C140 700 320 770 520 755 C780 735 1000 590 1200 620 L1200 760 L0 760Z" fill="url(#gw)"/>
    <path d="M0 620 C150 690 330 735 520 730 C780 722 1000 610 1200 635 L1200 760 L0 760Z" fill="#fff"/>
  </svg>
  <div class="brand abs" style="left:110px;top:60px;font-size:22px">
    <span class="brand-dot" style="width:48px;height:48px"></span>
    <span>Mended<br>Cherished<br>Whole</span>
  </div>
  <a class="btn" style="left:921px;top:58px;width:168px;height:40px">Give Now</a>
  <nav class="nav-links"><span>Home</span><span>About Us</span><span>Meetings &amp; Events</span><span>Encounter</span><span>Healing Rooms / Ministry</span></nav>
  <h1 class="abs">MENDED, CHERISHED,<br>WHOLE</h1>
  <p class="abs">Honoring God's presence by loving the broken, saving the lost, and healing the hurting through the demonstration of His love and power.</p>
  <a class="btn" style="left:110px;top:499px;width:168px;height:40px">Give Online</a>
</section>

<!-- MISSION -->
<section class="mission">
  <div class="mission-art abs" role="img" aria-label="Golden ministry emblem artwork"></div>
  <h2 class="section-title abs">OUR MISSION &amp;<br>VISION</h2>
  <p class="abs" style="top:1022px">Honoring God's presence by loving the broken, saving the lost, and healing the hurting through the demonstration of His love and power.</p>
  <p class="abs" style="top:1155px">Mended, Cherished, Whole is here to activate, proclaim and teach the love of the Father through Jesus with the guidance of the Holy Spirit.</p>
  <a class="btn" style="left:667px;top:1278px;width:132px;height:42px">Read More</a>
</section>

<!-- WHY -->
<section class="why">
  <h2 class="section-title abs">WHY CHOOSE US?</h2>
  <p class="lead abs">Through teaching, activation, and discipleship, we help people encounter God<br>and walk confidently in their identity and purpose.</p>

  <div class="feature" style="left:143px;top:1624px">
    <div class="icon"><svg width="60" height="60" viewBox="0 0 60 60"><rect x="22" y="4" width="16" height="52" rx="8" fill="#0f7a5a" transform="rotate(45 30 30)"/><rect x="22" y="4" width="16" height="52" rx="8" fill="#0a5e44" transform="rotate(-45 30 30)"/><rect x="24" y="24" width="12" height="12" fill="#fff" transform="rotate(45 30 30)"/></svg></div>
    <h3>HEARTS DESERVE<br>HEALING</h3>
    <p>At Mended, Cherished, Whole, we don't just talk about God's love - we demonstrate it, live it, and invite others to experience it.</p>
  </div>
  <div class="feature" style="left:378px;top:1589px">
    <div class="icon"><svg width="56" height="56" viewBox="0 0 56 56"><rect x="14" y="10" width="26" height="26" rx="9" fill="#0f7a5a"/><rect x="20" y="34" width="16" height="16" rx="3" fill="#0a5e44"/><path d="M40 20 l8 -6" stroke="#0f7a5a" stroke-width="6" stroke-linecap="round"/></svg></div>
    <h3>WE LEAD WITH THE<br>FATHER'S HEART</h3>
    <p>We carry a heart for the broken and a passion to see lives transformed through Jesus.</p>
  </div>
  <div class="feature" style="left:612px;top:1624px">
    <div class="icon"><svg width="56" height="56" viewBox="0 0 56 56"><path d="M28 48 C8 40 8 18 28 8 C48 18 48 40 28 48Z" fill="#0f7a5a"/><path d="M28 14 V46" stroke="#fff" stroke-width="3"/></svg></div>
    <h3>HEALING THROUGH<br>THE POWER</h3>
    <p>We create space for the Holy Spirit to move in freedom, bringing restoration to hearts, minds, and bodies.</p>
  </div>
  <div class="feature" style="left:847px;top:1589px">
    <div class="icon"><svg width="60" height="60" viewBox="0 0 60 60"><path d="M24 48 C6 36 4 22 12 16 C18 12 24 16 24 20 C24 16 30 12 36 16 C44 22 42 36 24 48Z" fill="#0a5e44"/><path d="M38 44 C28 37 27 29 31 26 C34 24 38 26 38 28 C38 26 42 24 45 26 C49 29 48 37 38 44Z" fill="#1aa487"/></svg></div>
    <h3>AUTHENTIC LOVE IN<br>ACTION</h3>
    <p>We minister with compassion, humility, and genuine care — reflecting Jesus in every encounter.</p>
  </div>
</section>

<!-- STORIES OF HEALING -->
<section class="stories">
  <svg class="stories-band abs" width="1200" height="960" viewBox="0 0 1200 960">
    <defs><linearGradient id="gb" x1="0" y1="0" x2="1" y2="1"><stop offset="0" stop-color="#0a5e44"/><stop offset="1" stop-color="#12876a"/></linearGradient></defs>
    <path d="M0 60 C160 140 330 140 520 100 C760 50 940 0 1200 10 L1200 880 C1000 950 860 940 700 910 C480 870 280 860 160 880 C90 892 40 905 0 910Z" fill="url(#gb)"/>
  </svg>
  <h2 class="abs">STORIES OF HEALING</h2>
  <p class="lead abs">Real testimonies from our healing rooms and gatherings — lives restored,<br>hearts made new, and families touched by the Father's love.</p>
  <article class="story-card" style="left:110px"><div class="photo" role="img" aria-label="Photo of a congregation standing in worship" style="background:linear-gradient(160deg,#4a4a5c,#2e2a3a)"></div><h3>Nothing is incurable<br>for God</h3></article>
  <article class="story-card" style="left:360px"><div class="photo" role="img" aria-label="Photo of worshippers raising hands in praise" style="background:linear-gradient(160deg,#5a3a3a,#2a1c24)"></div><h3>Healing amidst the<br>car accident</h3></article>
  <article class="story-card" style="left:609px"><div class="photo" role="img" aria-label="Photo of people praying together in a chapel" style="background:linear-gradient(160deg,#5c5a64,#33303a)"></div><h3>Why is healing<br>important?</h3></article>
  <article class="story-card" style="left:859px"><div class="photo" role="img" aria-label="Photo of two hands reaching toward each other in sunlight" style="background:linear-gradient(160deg,#e8ecef,#c9b38a 55%,#5b6a3c)"></div><h3>Now is the time to<br>move!</h3></article>
  <a class="btn btn-light" style="left:509px;top:2696px;width:182px;height:40px">Read More Stories</a>
</section>

<!-- SOCIAL FEED -->
<section class="feed">
  <h2 class="section-title abs">FOLLOW US ON GATHERLY</h2>
  <div class="feed-photo" role="img" aria-label="Photo of the brick church building at dusk" style="left:110px;background:linear-gradient(180deg,#3a4a6a,#7a3f30 60%,#3a2a22)"></div>
  <div class="feed-photo" role="img" aria-label="Photo of three women smiling together" style="left:360px;background:linear-gradient(180deg,#1f3a5a,#8a6a6a 60%,#3a2c30)"></div>
  <div class="feed-photo" role="img" aria-label="Photo of people praying outdoors on a field" style="left:609px;background:linear-gradient(180deg,#a8bcd4,#6a7a5a 65%,#4a5a3a)"></div>
  <div class="feed-photo" role="img" aria-label="Photo of an outdoor gathering beside a brick building" style="left:859px;background:linear-gradient(180deg,#7a3a30,#9a8a7a 55%,#5a7a3a)"></div>
  <a class="btn" style="left:535px;top:3431px;width:130px;height:42px">Follow Us</a>
</section>

<!-- NEWSLETTER -->
<section class="news">
  <svg class="abs" style="left:548px;top:3548px" width="104" height="94" viewBox="0 0 104 94">
    <path d="M0 36 L52 2 L104 36 V94 H0Z" fill="#0a5e44"/>
    <rect x="18" y="10" width="68" height="52" fill="#fff"/>
    <rect x="28" y="20" width="48" height="5" fill="#0f7a5a"/>
    <rect x="28" y="31" width="48" height="5" fill="#0f7a5a"/>
    <rect x="28" y="42" width="34" height="5" fill="#0f7a5a"/>
    <path d="M0 36 L52 70 L104 36 V94 H0Z" fill="#12876a"/>
  </svg>
  <h2 class="section-title abs">JOIN OUR NEWSLETTER</h2>
  <p class="abs">Receive gathering dates, healing room hours, new testimonies and journal prompts<br>delivered to your inbox. We send gentle updates and never share your address.</p>
  <div class="email-field abs">Enter Email Address</div>
  <a class="btn" style="left:720px;top:3795px;width:208px;height:52px;border-radius:26px;font-size:15px">Subscribe Now</a>
</section>

<!-- FOOTER -->
<svg class="footer-wave abs" width="1200" height="190" viewBox="0 0 1200 190">
  <defs><linearGradient id="gf" x1="0" x2="1"><stop offset="0" stop-color="#0a5e44"/><stop offset="1" stop-color="#1aa487"/></linearGradient></defs>
  <path d="M0 90 C300 30 700 160 1200 20 L1200 190 L0 190Z" fill="url(#gf)"/>
  <path d="M0 120 C300 110 500 150 800 130 C960 118 1100 90 1200 60 L1200 190 L0 190Z" fill="#fff"/>
  <path d="M0 140 C300 170 600 200 900 150 C1020 130 1120 110 1200 100 L1200 190 L0 190Z" fill="#0d0d0d"/>
</svg>
<footer class="footer abs">
  <div class="brand abs" style="left:110px;top:80px;font-size:34px;font-weight:600">
    <span class="brand-dot" style="width:70px;height:70px"></span>
    <span>Mended<br>Cherished<br>Whole</span>
  </div>
  <h4 style="left:451px;top:86px">QUICK LINKS</h4>
  <ul style="left:451px;top:122px"><li><span class="bullet"></span>Home</li><li><span class="bullet"></span>About Us</li><li><span class="bullet"></span>Meetings &amp; Events</li><li><span class="bullet"></span>Healing Rooms</li><li><span class="bullet"></span>Give</li></ul>
  <h4 style="left:646px;top:86px">CONTACT INFO</h4>
  <ul style="left:646px;top:122px;width:300px">
    <li style="align-items:flex-start;height:72px;line-height:36px"><svg width="12" height="16" viewBox="0 0 12 16" style="margin-top:10px;flex:none"><path d="M6 0a6 6 0 0 1 6 6c0 4-6 10-6 10S0 10 0 6a6 6 0 0 1 6-6z" fill="#fff"/><circle cx="6" cy="6" r="2" fill="#0d0d0d"/></svg><span>412 Willow Creek Lane, Fairhaven,<br>OH, United States, 45099</span></li>
    <li><svg width="14" height="11" viewBox="0 0 14 11" style="flex:none"><rect width="14" height="11" fill="#fff"/><path d="M0 0 L7 6 L14 0" stroke="#0d0d0d" fill="none"/></svg>hello@mendedcherishedwhole.org</li>
    <li><svg width="13" height="13" viewBox="0 0 13 13" style="flex:none"><path d="M2 0 L5 3 L3.5 5 C4.5 7 6 8.5 8 9.5 L10 8 L13 11 L11 13 C5 12 1 8 0 2Z" fill="#fff"/></svg>+1 555-218-4470</li>
  </ul>
  <h4 style="left:968px;top:86px">FOLLOW US</h4>
  <ul style="left:968px;top:122px"><li><span class="bullet" style="border-radius:2px"></span>Gatherly</li><li><span class="bullet" style="border-radius:2px"></span>Chirper</li><li><span class="bullet" style="border-radius:2px"></span>Snapgram</li></ul>
</footer>
<div class="rule abs"></div>
<a class="btn" style="left:948px;top:4346px;width:140px;height:36px;font-size:14px">Let's Talk</a>
<div class="copy abs">(C) Copyright 2025 | All Rights Reserved</div>

</body>
</html>
```